Global (re)insurance broker needs a business card design

We need a classic business card for our company that is headquartered in SG, with offices in Malaysia and Dubai. We specialise in insurance and reinsurance broking and consultancy for our global clients.

```html
<!DOCTYPE html>
<html lang="en">
<head>
<meta charset="utf-8">
<title>Norvale Business Card</title>
<link rel="stylesheet" href="https://fonts.googleapis.com/css2?family=Open+Sans:wght@400;600;700;800&display=swap">
<style>
  :root {
    --bg: #2a2a2e;
    --brand-blue: #284a9a;
    --card-black: #161616;
    --mint: #c3dfbd;
    --white: #ffffff;
  }
  * { margin: 0; padding: 0; box-sizing: border-box; }
  html, body {
    width: 1200px;
    height: 947px;
    overflow: hidden;
    background: var(--bg);
    font-family: "Open Sans", Arial, sans-serif;
  }
  .card {
    position: absolute;
    left: 240px;
    width: 720px;
    height: 412px;
    border-radius: 26px;
    overflow: hidden;
  }
  .card--front {
    top: 40px;
    background: var(--brand-blue);
    display: flex;
    align-items: center;
    justify-content: center;
  }
  .front-wordmark {
    color: var(--white);
    font-weight: 800;
    font-size: 118px;
    letter-spacing: 4px;
  }
  .card--back {
    top: 495px;
    background: var(--brand-blue);
  }
  .back-panel {
    position: absolute;
    inset: 0;
    width: 100%;
    height: 100%;
  }
  .back-wordmark {
    position: absolute;
    left: 70px;
    top: 160px;
    color: var(--mint);
    font-weight: 800;
    font-size: 58px;
    letter-spacing: 2px;
  }
  .divider {
    position: absolute;
    left: 380px;
    top: 70px;
    width: 2px;
    height: 236px;
    background: var(--mint);
  }
  .details {
    position: absolute;
    left: 410px;
    top: 54px;
    color: var(--white);
  }
  .details__name {
    color: var(--brand-blue);
    font-weight: 800;
    font-size: 26px;
    line-height: 1.1;
  }
  .details__title {
    font-size: 17px;
    margin-bottom: 16px;
  }
  .contact-list { list-style: none; margin-bottom: 18px; }
  .contact-list li {
    display: flex;
    align-items: center;
    gap: 8px;
    font-size: 16px;
    line-height: 1.45;
  }
  .contact-list svg { width: 13px; height: 13px; fill: var(--white); flex: none; }
  .details__address {
    font-style: normal;
    font-size: 16px;
    line-height: 1.4;
  }
</style>
</head>
<body>

  <section class="card card--front" aria-label="Card front">
    <div class="front-wordmark">NORVALE</div>
  </section>

  <section class="card card--back" aria-label="Card back">
    <svg class="back-panel" viewBox="0 0 720 412" preserveAspectRatio="none" aria-hidden="true">
      <path d="M6 6 H714 V200 C650 310 500 340 360 372 C300 386 270 396 255 406 H6 Z" fill="var(--card-black)"/>
      <path d="M714 168 C650 295 500 330 360 364 C300 378 268 392 250 406 L255 406 C270 396 300 386 360 372 C500 340 650 310 714 200 Z" fill="var(--mint)"/>
    </svg>
    <div class="back-wordmark">NORVALE</div>
    <div class="divider"></div>
    <div class="details">
      <p class="details__name">Marina Koh</p>
      <p class="details__title">Chief Operating Officer</p>
      <ul class="contact-list">
        <li><svg viewBox="0 0 16 16"><path d="M3 1l3 3-2 2c1 2 3 4 5 5l2-2 3 3-2 3C6 14 2 10 1 3z"/></svg>+65 9123 4580</li>
        <li><svg viewBox="0 0 16 16"><path d="M1 3h14v10H1z M1 3l7 6 7-6" stroke="#161616" stroke-width="1"/></svg>marina@norvale.com</li>
        <li><svg viewBox="0 0 16 16"><circle cx="8" cy="8" r="7"/></svg>www.norvale.com</li>
      </ul>
      <address class="details__address">
        28 Harbour Lane,<br>
        Meridian Tower #08-04,<br>
        Singapore 048620
      </address>
    </div>
  </section>

</body>
</html>
```